Cocktail-Making Assistant App re-design

Ok boys and girls, here's the deal:
I have an android app which is almost complete, but needs a design overhaul.

The app is a standard cocktail-making assistant: gives you a list of cocktails and the ability to see which cocktail you can make out of those ingredients (drinks, fruit, etc) you have at home.

I've attached some general app flow, as well as detailed requirements/explanation presentation. Most of those things are just FYI, so that you know what it's about.

3 screens are the most important (main screen, cocktail view screen, ingredient view screen), meaning I will pick the design mostly based on ideas for those 3 things, with the fourth being a rather simple list (given on attached flow, third tier)
Some other screens are derived from that, with some minor changes on it, but you shouldn't care about that.

There are lots of other, non-explained things which I said nothing about only because they are (from design point of view) completely the same and would only make it seem more complicated.

I don't want to influence the colour scheme, but the app will be released under RedFig developer name (having a light colured red fig as a logo) so I suppose some brownish design, for example, will not really fit nicely. If you, however, have a killer which you are confident will prove me wrong, I'm looking forward to seeing it!

It should be a serious, elegant look (as opposed to cartoonish, but we are not aiming for a business look at all!), not cluttered with details, no clubbing themes, glitter and so on.

Test apk file available on request (Android 2.3+).

Edit: payment is now guaranteed
Also please note that currently, the favorite, "heart" button has a motion effect:
on click it flies out of the screen to the left (white heart) and comes back to the screen as a red heart. Take that into consideration, if it means anything to you.

Target Market(s)

Whoever you imagine would enjoy drinking cocktails

Industry/Entity Type

Business

Requirements
Must have
• Everything is said in the provided documentation - images say more than I could possibly write here.
Nice to have
• As said, most of the icons are a nice-to-have. Only those which are critically linked to the rest of the design must be provided. More details in the docs.
Should not have
• No cartoon look, No zillion colours

```html
<!DOCTYPE html>
<html lang="en">
<head>
<meta charset="utf-8">
<title>Cocktail Search – Ingredient View</title>
<link href="https://fonts.googleapis.com/css2?family=Quicksand:wght@400;500&display=swap" rel="stylesheet">
<style>
  :root {
    --page-bg: #e6e7e9;
    --screen-bg: #f3f3f3;
    --screen-glow: #ffffff;
    --header-top: #66b9da;
    --header-bottom: #a7d2e2;
    --rule: #e2e2e2;
    --ink: #2c2c2c;
    --ink-soft: #777777;
    --icon: #6e6e6e;
    --bubble: #cfe3f2;
    --tile-bar: #a2e6d0;
    --tile-list: #cfe3f2;
    --tile-featured: #d5cbd0;
    --white: #ffffff;
  }
  * { box-sizing: border-box; margin: 0; padding: 0; }
  html, body {
    width: 1200px; height: 1003px; overflow: hidden;
    background: var(--page-bg);
    font-family: "Quicksand", "Helvetica Neue", Arial, sans-serif;
  }
  .screen {
    position: absolute; top: 4px; width: 558px; height: 987px;
    background: radial-gradient(ellipse at 50% 45%, var(--screen-glow) 40%, var(--screen-bg) 100%);
    overflow: hidden;
  }
  .screen--text { left: 23px; }
  .screen--photo { left: 609px; }

  .app-bar {
    position: absolute; left: 0; top: 0; width: 100%; height: 92px;
    background: linear-gradient(180deg, var(--header-top), var(--header-bottom));
  }
  .app-bar__title {
    position: absolute; left: 0; right: 0; top: 23px; text-align: center;
    color: var(--white); font-size: 36px; font-weight: 400; letter-spacing: 0.3px;
  }
  .app-bar__button { position: absolute; top: 17px; width: 58px; height: 58px; }
  .app-bar__button--home { left: 15px; }
  .app-bar__button--settings { right: 15px; }

  .rule { position: absolute; left: 20px; right: 20px; height: 3px; background: var(--rule); }

  .ingredient-head__icon { position: absolute; left: 23px; top: 173px; width: 100px; height: 100px; }
  .ingredient-head__name {
    position: absolute; left: 160px; top: 185px; font-size: 29px; font-weight: 400; color: var(--ink);
  }
  .ingredient-head__meta {
    position: absolute; left: 160px; top: 227px; font-size: 14px; line-height: 21px; color: var(--ink-soft);
  }

  .description { position: absolute; left: 30px; right: 30px; text-align: center; color: var(--ink-soft); }
  .description p + p { margin-top: 33px; }
  .screen--text .description { top: 365px; font-size: 23px; line-height: 33px; }
  .screen--photo .description { top: 539px; font-size: 19px; line-height: 26px; }
  .screen--photo .description p + p { margin-top: 26px; }

  .photo-slot {
    position: absolute; left: 157px; top: 311px; width: 210px; height: 210px; border-radius: 50%;
    background: var(--bubble); display: flex; align-items: center; justify-content: center;
    text-align: center; font-size: 20px; line-height: 26px; font-weight: 500; color: #555555;
  }

  .similar {
    position: absolute; left: 0; right: 0; top: 780px; text-align: center;
    font-size: 27px; color: #555555;
  }

  .nav { position: absolute; left: 12px; top: 827px; width: 534px; height: 108px; display: flex; }
  .nav__tile { flex: 1; position: relative; }
  .nav__tile--bar { background: var(--tile-bar); }
  .nav__tile--list { background: var(--tile-list); }
  .nav__tile--featured { background: var(--tile-featured); }
  .nav__tile svg { position: absolute; left: 50%; top: 24px; transform: translateX(-50%); }
  .nav__label {
    position: absolute; left: 0; right: 0; bottom: 6px; text-align: center;
    font-size: 13.5px; color: #555555;
  }
</style>
</head>
<body>

<!-- Ingredient view, text only -->
<section class="screen screen--text">
  <header class="app-bar">
    <svg class="app-bar__button app-bar__button--home" viewBox="0 0 58 58">
      <circle cx="29" cy="29" r="26.5" fill="none" stroke="var(--white)" stroke-width="3.5"/>
      <path d="M16 30 L29 18 L42 30 H38 V40 H20 V30 Z" fill="var(--white)"/>
    </svg>
    <h1 class="app-bar__title">Cocktail Search</h1>
    <svg class="app-bar__button app-bar__button--settings" viewBox="0 0 58 58">
      <circle cx="29" cy="29" r="26.5" fill="none" stroke="var(--white)" stroke-width="3.5"/>
      <circle cx="29" cy="29" r="10" fill="none" stroke="var(--white)" stroke-width="7" stroke-dasharray="4 3.85"/>
      <circle cx="29" cy="29" r="9" fill="var(--white)"/>
      <circle cx="29" cy="29" r="4" fill="var(--header-top)"/>
    </svg>
  </header>

  <div class="rule" style="top:160px"></div>
  <svg class="ingredient-head__icon" viewBox="0 0 100 100">
    <circle cx="50" cy="50" r="50" fill="var(--bubble)"/>
    <path d="M29 36 H65 L47 57 Z" fill="none" stroke="var(--icon)" stroke-width="3.5" stroke-linejoin="round"/>
    <path d="M47 57 V76 M38 78 H56" stroke="var(--icon)" stroke-width="4" stroke-linecap="round"/>
    <path d="M45 50 L60 22 L66 18" fill="none" stroke="var(--icon)" stroke-width="3.5" stroke-linecap="round"/>
  </svg>
  <h2 class="ingredient-head__name">Dalby’s Irish Cream</h2>
  <p class="ingredient-head__meta">Type - Liquor / Cordial<br>Alc - 17 . 0</p>
  <div class="rule" style="top:286px"></div>

  <div class="description">
    <p>Dalby’s Irish Cream and some more<br>sample text is placed here and so<br>on sample text.</p>
    <p>Lorem ipsum dolor sit amet ipsum<br>dolor sit amet - sample text is<br>placed here sample text<br>is placed here</p>
  </div>

  <div class="rule" style="top:776px"></div>
  <p class="similar">2 similar ingredients</p>
  <div class="rule" style="top:818px"></div>

  <nav class="nav">
    <div class="nav__tile nav__tile--bar">
      <svg width="86" height="62" viewBox="0 0 86 62" fill="none" stroke="var(--icon)" stroke-width="2.5">
        <path d="M8 2 H14 V14 L19 24 V60 H3 V24 L8 14 Z"/>
        <path d="M30 2 H36 V14 L41 24 V60 H25 V24 L30 14 Z"/>
        <path d="M51 24 H75 C75 40 68 46 63 46 C58 46 51 40 51 24 Z M63 46 V59 M55 60 H71"/>
      </svg>
      <span class="nav__label">My Bar</span>
    </div>
    <div class="nav__tile nav__tile--list">
      <svg width="70" height="52" viewBox="0 0 70 52" fill="none" stroke="var(--icon)" stroke-width="3">
        <path d="M2 6 H12 L20 34 H56 L66 10 H16"/>
        <circle cx="26" cy="44" r="4.5" fill="var(--icon)"/>
        <circle cx="50" cy="44" r="4.5" fill="var(--icon)"/>
      </svg>
      <span class="nav__label">Shopping List</span>
    </div>
    <div class="nav__tile nav__tile--featured">
      <svg width="40" height="62" viewBox="0 0 40 62">
        <path d="M12 26 L4 56 L12 50 L16 60 L20 34 Z M28 26 L36 56 L28 50 L24 60 L20 34 Z" fill="var(--icon)"/>
        <circle cx="20" cy="18" r="15" fill="var(--icon)"/>
        <circle cx="20" cy="18" r="9" fill="none" stroke="var(--tile-featured)" stroke-width="2"/>
      </svg>
      <span class="nav__label">Featured</span>
    </div>
  </nav>
  <div class="rule" style="top:946px"></div>
</section>

<!-- Ingredient view, with photo -->
<section class="screen screen--photo">
  <header class="app-bar">
    <svg class="app-bar__button app-bar__button--home" viewBox="0 0 58 58">
      <circle cx="29" cy="29" r="26.5" fill="none" stroke="var(--white)" stroke-width="3.5"/>
      <path d="M16 30 L29 18 L42 30 H38 V40 H20 V30 Z" fill="var(--white)"/>
    </svg>
    <h1 class="app-bar__title">Cocktail Search</h1>
    <svg class="app-bar__button app-bar__button--settings" viewBox="0 0 58 58">
      <circle cx="29" cy="29" r="26.5" fill="none" stroke="var(--white)" stroke-width="3.5"/>
      <circle cx="29" cy="29" r="10" fill="none" stroke="var(--white)" stroke-width="7" stroke-dasharray="4 3.85"/>
      <circle cx="29" cy="29" r="9" fill="var(--white)"/>
      <circle cx="29" cy="29" r="4" fill="var(--header-top)"/>
    </svg>
  </header>

  <div class="rule" style="top:160px"></div>
  <svg class="ingredient-head__icon" viewBox="0 0 100 100">
    <circle cx="50" cy="50" r="50" fill="var(--bubble)"/>
    <path d="M29 36 H65 L47 57 Z" fill="none" stroke="var(--icon)" stroke-width="3.5" stroke-linejoin="round"/>
    <path d="M47 57 V76 M38 78 H56" stroke="var(--icon)" stroke-width="4" stroke-linecap="round"/>
    <path d="M45 50 L60 22 L66 18" fill="none" stroke="var(--icon)" stroke-width="3.5" stroke-linecap="round"/>
  </svg>
  <h2 class="ingredient-head__name">Dalby’s Irish Cream</h2>
  <p class="ingredient-head__meta">Type - Liquor / Cordial<br>Alc - 17 . 0</p>
  <div class="rule" style="top:286px"></div>

  <div class="photo-slot" role="img" aria-label="Round photo of the ingredient bottle">Photo<br>placed<br>here</div>

  <div class="description">
    <p>Dalby’s Irish Cream and some more<br>sample text is placed here and so<br>on sample text.</p>
    <p>Lorem ipsum dolor sit amet ipsum<br>dolor sit amet - sample text is<br>placed here sample text<br>is placed here</p>
  </div>

  <div class="rule" style="top:776px"></div>
  <p class="similar">2 similar ingredients</p>
  <div class="rule" style="top:818px"></div>

  <nav class="nav">
    <div class="nav__tile nav__tile--bar">
      <svg width="86" height="62" viewBox="0 0 86 62" fill="none" stroke="var(--icon)" stroke-width="2.5">
        <path d="M8 2 H14 V14 L19 24 V60 H3 V24 L8 14 Z"/>
        <path d="M30 2 H36 V14 L41 24 V60 H25 V24 L30 14 Z"/>
        <path d="M51 24 H75 C75 40 68 46 63 46 C58 46 51 40 51 24 Z M63 46 V59 M55 60 H71"/>
      </svg>
      <span class="nav__label">My Bar</span>
    </div>
    <div class="nav__tile nav__tile--list">
      <svg width="70" height="52" viewBox="0 0 70 52" fill="none" stroke="var(--icon)" stroke-width="3">
        <path d="M2 6 H12 L20 34 H56 L66 10 H16"/>
        <circle cx="26" cy="44" r="4.5" fill="var(--icon)"/>
        <circle cx="50" cy="44" r="4.5" fill="var(--icon)"/>
      </svg>
      <span class="nav__label">Shopping List</span>
    </div>
    <div class="nav__tile nav__tile--featured">
      <svg width="40" height="62" viewBox="0 0 40 62">
        <path d="M12 26 L4 56 L12 50 L16 60 L20 34 Z M28 26 L36 56 L28 50 L24 60 L20 34 Z" fill="var(--icon)"/>
        <circle cx="20" cy="18" r="15" fill="var(--icon)"/>
        <circle cx="20" cy="18" r="9" fill="none" stroke="var(--tile-featured)" stroke-width="2"/>
      </svg>
      <span class="nav__label">Featured</span>
    </div>
  </nav>
  <div class="rule" style="top:946px"></div>
</section>

</body>
</html>
```